Computer consultant business card

Bexil Software is a newly started computer consulting company. It's a small one-man company that provides mostly Vornix applications but also websites in collaboration with designers. I'm running this company on the side of full time university studies.

I want the final design to be clean and memorable. Be creative! :)

Some inspiration:
http://www.pixelmarta.com/design/48317
http://www.pixelmarta.com/design/2739164/business-card-design-by-frostlynk
http://www.pixelmarta.com/design/604281/business-card-design-by-koralind-vestrabanu

See attachment for my company logo.
Updates

I would like to thank everyone for submitting! I'll need a couple of days to review and ultimately select a design.

Target Market(s)

Non-technical entrepreneurs and small companies.

Industry/Entity Type

University

Requirements
Must have
• My company logo.
In any way, both colors from my logo.
First- and last name, e-mail and phone number.
Double-sided design.
Nice to have
• Something creative with the symbol in my logo

```html
<!DOCTYPE html>
<html lang="en">
<head>
<meta charset="utf-8">
<title>Business Card — Front and Back</title>
<link href="https://fonts.googleapis.com/css2?family=Didact+Gothic&display=swap" rel="stylesheet">
<style>
  :root {
    --stage: #2a2a2c;
    --card-white: #f6f6f6;
    --card-white-edge: #e4e4e4;
    --brand-blue: #4a74b8;
    --brand-blue-light: #76a6da;
    --brand-blue-deep: #3a5fa0;
    --brand-black: #1e1e20;
    --text-grey: #5a5a5a;
  }
  * { margin: 0; padding: 0; box-sizing: border-box; }
  html, body { width: 1200px; height: 900px; overflow: hidden; }
  body {
    background: var(--stage);
    font-family: "Didact Gothic", "Century Gothic", sans-serif;
    position: relative;
  }
  .card {
    position: absolute;
    width: 560px;
    height: 320px;
    box-shadow: 0 14px 30px rgba(0,0,0,.5);
    overflow: hidden;
  }
  /* Front side */
  .card--front {
    left: 110px;
    top: 110px;
    background: radial-gradient(ellipse at 55% 45%, #ffffff 0%, var(--card-white) 55%, var(--card-white-edge) 100%);
  }
  .card--front .edge-line {
    position: absolute; left: 0; right: 0; bottom: 20px;
    height: 4px; background: var(--brand-black);
  }
  .card--front .edge-band {
    position: absolute; left: 0; right: 0; bottom: 0;
    height: 16px; background: var(--brand-blue);
  }
  .wordmark {
    position: absolute; top: 30px; right: 34px;
    display: flex; align-items: center; gap: 8px;
    font-size: 30px; color: var(--brand-black); letter-spacing: .5px;
    line-height: 1;
  }
  .wordmark .mark-dot {
    width: 22px; height: 22px; border-radius: 50%;
    background: var(--brand-blue);
  }
  .identity {
    position: absolute; left: 40px; bottom: 62px;
  }
  .identity .name { color: var(--brand-blue); font-size: 17px; }
  .identity .role { color: var(--text-grey); font-size: 13px; margin-top: 2px; }
  .contacts {
    position: absolute; left: 300px; bottom: 56px;
    list-style: none;
    color: var(--text-grey); font-size: 13px;
  }
  .contacts li { display: flex; align-items: center; gap: 8px; height: 17px; }
  .contacts svg { width: 12px; height: 12px; fill: none; stroke: var(--brand-blue); stroke-width: 1.6; }

  /* Back side */
  .card--back {
    left: 530px;
    top: 470px;
    background: radial-gradient(ellipse at 50% 38%, var(--brand-blue-light) 0%, var(--brand-blue) 55%, var(--brand-blue-deep) 100%);
    display: flex; flex-direction: column; align-items: center; justify-content: center;
  }
  .back-mark {
    display: flex; align-items: center; gap: 14px;
    font-size: 46px; color: var(--brand-black); line-height: 1;
  }
  .back-mark .mark-dot {
    width: 40px; height: 40px; border-radius: 50%;
    background: var(--brand-black);
  }
  .website {
    margin-top: 44px; color: #ffffff; font-size: 16px; letter-spacing: .5px;
  }
</style>
</head>
<body>
  <section class="card card--front" aria-label="Card front">
    <div class="wordmark"><span class="mark-dot"></span><span>qelvr</span></div>

    <div class="identity">
      <p class="name">Your Name Here</p>
      <p class="role">Designation</p>
    </div>

    <ul class="contacts">
      <li>
        <svg viewBox="0 0 12 12"><path d="M3 1.5 L4.8 4 L3.8 5.2 Q5 7.4 6.8 8.2 L8 7.2 L10.5 9 L9.4 10.6 Q4.5 10.2 1.5 3 Z"/></svg>
        <span>00-123-4567</span>
      </li>
      <li>
        <svg viewBox="0 0 12 12"><rect x="3" y="1.5" width="6" height="3.5"/><rect x="1.5" y="5" width="9" height="4"/><rect x="3" y="8" width="6" height="2.5"/></svg>
        <span>00-123-4567</span>
      </li>
      <li>
        <svg viewBox="0 0 12 12"><rect x="1.5" y="3" width="9" height="6.5"/><path d="M1.5 3 L6 7 L10.5 3"/></svg>
        <span>name@yourdomain.com</span>
      </li>
    </ul>

    <div class="edge-line"></div>
    <div class="edge-band"></div>
  </section>

  <section class="card card--back" aria-label="Card back">
    <div class="back-mark"><span class="mark-dot"></span><span>qelvr</span></div>
    <p class="website">www.<strong>yourdomain</strong>.com</p>
  </section>
</body>
</html>
```